Brightmill Data Works

Our company is about IT hardwares and IT solutions. IT hardware such as PC, RAMS, storage and servers. IT solutions such as project management, BA. We are also selling new technology too.

Target Market(s)

Consumer, Small to Medium Business, Corporate

Requirements
Must have
• The business card must have the following:
• Name:
• Title:
• Contact Number:
• Email address:
• Website:
• Color: Must match the logo color upgrade

```html
<!DOCTYPE html>
<html lang="en">
<head>
<meta charset="utf-8">
<title>Brightmill Data Works – Business Card</title>
<link rel="stylesheet" href="https://fonts.googleapis.com/css2?family=Lato:wght@400;700&family=Saira+Semi+Condensed:wght@700&display=swap">
<style>
  :root {
    --backdrop: #3b322d;
    --card: #121212;
    --card-edge: #1c1c1c;
    --accent: #e08a2a;
    --ink: #f2f2f2;
    --silver: #cfcfcf;
    --rule: #3a3a3a;
  }
  * { margin: 0; padding: 0; box-sizing: border-box; }
  html, body {
    width: 1200px; height: 844px; overflow: hidden;
    background: var(--backdrop);
  }
  .stage {
    position: relative; width: 1200px; height: 844px;
    display: flex; align-items: center; justify-content: center; gap: 60px;
  }
  .card {
    width: 520px; height: 298px;
    background: var(--card);
    border: 1px solid var(--card-edge);
    box-shadow: 0 12px 30px rgba(0,0,0,0.45);
    position: relative;
  }
  .card--contact { display: flex; align-items: center; }
  .brand {
    width: 268px; display: flex; align-items: center; justify-content: center; gap: 10px;
  }
  .brand-mark { width: 14px; height: 14px; background: var(--accent); flex: none; }
  .brand-name {
    font-family: "Saira Semi Condensed", sans-serif; font-weight: 700;
    font-size: 22px; line-height: 1.05; letter-spacing: 0.5px;
    color: var(--ink); text-transform: uppercase;
  }
  .divider { width: 1px; height: 110px; background: var(--rule); }
  .details { padding-left: 28px; font-family: "Lato", sans-serif; color: var(--ink); }
  .person-name {
    font-size: 19px; font-weight: 400; color: var(--accent);
    text-transform: uppercase; letter-spacing: 0.3px;
  }
  .person-title { font-size: 14px; margin-bottom: 14px; }
  .contact-list { list-style: none; font-size: 14px; line-height: 1.55; }
  .contact-list li { display: flex; align-items: center; gap: 8px; }
  .contact-list svg { width: 11px; height: 11px; fill: var(--accent); flex: none; }
  .card--front { display: flex; align-items: center; justify-content: center; }
  .card--front .brand { width: auto; }
  .card--front .brand-name { font-size: 34px; color: var(--silver); text-align: center; }
  .card--front .brand-mark { background: var(--silver); width: 18px; height: 18px; }
</style>
</head>
<body>
<main class="stage">
  <section class="card card--contact">
    <div class="brand">
      <span class="brand-mark"></span>
      <span class="brand-name">Brightmill<br>Data Works</span>
    </div>
    <div class="divider"></div>
    <div class="details">
      <p class="person-name">Marcus Hale</p>
      <p class="person-title">Managing Director</p>
      <ul class="contact-list">
        <li><svg viewBox="0 0 24 24" aria-hidden="true"><path d="M6.6 10.8a15.1 15.1 0 0 0 6.6 6.6l2.2-2.2a1 1 0 0 1 1-.25 11.4 11.4 0 0 0 3.6.57 1 1 0 0 1 1 1V20a1 1 0 0 1-1 1A17 17 0 0 1 3 4a1 1 0 0 1 1-1h3.5a1 1 0 0 1 1 1c0 1.25.2 2.45.57 3.57a1 1 0 0 1-.25 1z"/></svg>044-987 650 321</li>
        <li><svg viewBox="0 0 24 24" aria-hidden="true"><path d="M2 5h20v14H2z M2 5l10 8 10-8" fill="var(--accent)"/></svg>info@brightmill.com</li>
        <li><svg viewBox="0 0 24 24" aria-hidden="true"><circle cx="12" cy="12" r="10"/></svg>www.brightmill.com</li>
      </ul>
    </div>
  </section>
  <section class="card card--front">
    <div class="brand">
      <span class="brand-mark"></span>
      <span class="brand-name">Brightmill<br>Data Works</span>
    </div>
  </section>
</main>
</body>
</html>
```